Corwin Beacon Lighting - Commercial & Residential Landscape Lighting

Landscape Lighting Services & Design: Create a website for our landscape lighting company. We would like the design to be tailored around this description:
Illuminate with Confidence. Designed with Precision. Installed with Care.
Locally and veteran-owned, we take pride in transforming outdoor spaces through innovative lighting solutions tailored to your vision. From landscape and holiday lighting to permanent installations, our effortless process and expert design deliver breathtaking results and lasting curb appeal. Backed by a lifetime warranty and quarterly service options, our commitment to quality and customer satisfaction is unwavering. Try before you buy and experience your home in a whole new light with our complimentary demo kit — see the stunning effects before you decide.
- Also, add in this information as well; Outdoor Lighting not only beautifies spaces but also significantly enhances safety by illuminating your home or business. Beautifully lit entrances deter potential intruders, making your home a safer place for your loved ones. we also offer quarterly service plans to ensure lighting equipment continues to operate & illuminate effectively throughout the year. Also mention we provide free estimates and we are offering a 10% discount to military, veterans, and first responders.

Target Market(s)

Luxury market

Industry/Entity Type

Landscape Lighting - Residential & Commercial Lighting Services

Coding

Coded - Design and coding required

Number of Pages Required

2 page

Colors
00AB8E
00BBA5
67D7C9
C6EFE9
E9F9F6
59FF00
82FF00
B8FF75
E3FFCB
F4FFEA
FFC000
F8CF3A
FAE287
FDF2CF
FEFAEE

Requirements
Must have
• a lead generation button where people can submit their information for us to reach out to them and schedule their free estimate, homepage, about page, contact page, products and services page, user friendly, easy to navigate, and it also must be engaging and eye popping, as well as appealing to the luxury market. Please use colors; verdent green, dark green, ivory, and sunny yellow. Also, include an about page that references our story; Derek is retired Army and he opened a fitness studio in 2017 with his wife Jolene. He has installed low voltage lighting in every home he lived in and for his friends and family over the years and decided to open his own business because he is passionate about beautifying outdoor landscapes and highlighting a properties full potential, not only in the day but at night as well all while providing safety and security for his clients. Having a deep respect for nature and landscaping, he wants to provide the same care and quality to each of his clients as he has in the fitness industry for decades. He believes small businesses are the back bone of America and he's excited to provide a service that is all to often neglected in the design of a home.
Nice to have
• I would like to have a clear intent and purpose, engaging web design, clear call to action, optimized for search engines, mobile friendy design, security measures, credibility indicators

```html
<!DOCTYPE html>
<html lang="en">
<head>
<meta charset="utf-8">
<title>Corwin Beacon Lighting</title>
<link href="https://fonts.googleapis.com/css2?family=Urbanist:wght@400;500;600;700&display=swap" rel="stylesheet">
<style>
:root{
  --stage:#eeeeee;
  --night:#0c1626;
  --dusk:#3a3414;
  --amber:#ffc000;
  --cream:#fdeaa4;
  --forest:#0e2a1f;
  --mist:#f4f5f3;
  --card:#f1f0ee;
  --ink:#1c1c1c;
  --white:#ffffff;
}
*{box-sizing:border-box;margin:0;padding:0}
html,body{width:1200px;height:675px;overflow:hidden}
body{background:var(--stage);font-family:"Urbanist",sans-serif;color:var(--ink);position:relative}
.frame{position:absolute;overflow:hidden;background:var(--white)}
.frame-hero{left:26px;top:188px;width:448px;height:253px}
.frame-top{left:520px;top:55px;width:329px;height:620px}
.frame-rest{left:859px;top:0;width:329px;height:675px}
.page{position:absolute;left:0;top:0;width:705px;transform-origin:0 0}
.frame-hero .page{transform:scale(.6355)}
.frame-top .page{transform:scale(.4667)}
.frame-rest .page{transform:scale(.4667) translateY(-296px)}

/* hero */
.hero{position:relative;height:446px;overflow:hidden;display:flex;flex-direction:column;align-items:center;justify-content:center;color:var(--white);text-align:center}
.frame-hero .hero{height:398px}
.hero-photo{position:absolute;inset:0;background:
  radial-gradient(ellipse at 50% 70%,rgba(255,190,60,.35),transparent 60%),
  linear-gradient(180deg,var(--night) 0%,#1a2431 45%,#4a3d16 85%,#6b5412 100%)}
.brand{position:absolute;left:48px;top:20px;display:flex;align-items:center;gap:6px;font-size:15px;font-weight:600;color:var(--white);z-index:2}
.brand-dot{width:8px;height:8px;border-radius:50%;background:var(--amber)}
.nav{position:absolute;right:29px;top:18px;display:flex;gap:5px;z-index:2}
.nav-links{display:flex;gap:9px;border:1px solid rgba(255,255,255,.8);border-radius:12px;padding:5px 9px;font-size:6px}
.nav-cta{background:var(--amber);color:var(--ink);border-radius:12px;padding:6px 13px;font-size:6px;font-weight:700}
.hero h1{position:relative;font-size:33px;font-weight:700;line-height:1.07;letter-spacing:.2px;margin-top:10px}
.hero p{position:relative;font-size:16px;line-height:1;margin-top:16px;max-width:430px}
.hero-actions{position:relative;display:flex;gap:17px;margin-top:34px}
.btn{display:inline-block;border-radius:17px;padding:10px 15px;font-size:10.5px;font-weight:700;width:137px;text-align:center}
.btn-gold{background:var(--amber);color:var(--ink)}
.btn-forest{background:var(--forest);color:var(--amber)}

/* about */
.about{position:relative;height:463px;background:linear-gradient(180deg,var(--cream) 0%,#fdd659 45%,var(--amber) 100%)}
.tag{position:absolute;left:57px;display:flex;gap:9px;font-size:7.5px;line-height:1.45}
.tag::before{content:"";flex:none;width:8px;height:8px;border-radius:50%;background:var(--ink);box-shadow:0 0 0 2px rgba(0,0,0,.15);margin-top:3px}
.lead{position:absolute;left:292px;width:335px;font-size:11.5px;line-height:1.35}
.more{position:absolute;left:292px;top:154px;width:284px;font-size:11.5px;padding-bottom:8px;border-bottom:1px solid var(--ink)}
.portrait{position:absolute;left:57px;top:161px;width:194px;height:260px;border:3px solid #fff6d2;border-radius:12px;padding:5px}
.photo{width:100%;height:100%;border-radius:9px;background:linear-gradient(180deg,#2a3b4a 0%,#54606a 25%,#b9703e 45%,#2c3a24 62%,#1c2a18 100%)}
.stat{position:absolute;left:292px}
.stat b{display:block;font-weight:400;font-size:29px;line-height:1}
.stat span{font-size:12px}
.stat-wide b{font-size:33px}

/* services */
.services{position:relative;height:537px;background:var(--mist)}
.grid{position:absolute;left:62px;top:160px;display:grid;grid-template-columns:repeat(4,138px);column-gap:8px}
.col{display:flex;flex-direction:column;gap:12px}
.col .photo{height:184px;border-radius:6px}
.svc{background:var(--white);border-radius:6px;padding:8px 6px;height:56px}
.svc h3{font-size:8px;font-weight:500;margin-bottom:4px}
.svc p{font-size:4px;line-height:1.5;color:#555}
.quote-row{position:absolute;left:62px;top:475px;width:577px;display:flex;align-items:center;justify-content:space-between;font-size:7px}
.quote-row .btn{width:277px;padding:8px 0;font-size:8.5px;border-radius:14px}

/* testimonials */
.reviews{position:relative;height:300px;background:var(--white)}
.reviews h2{position:absolute;left:0;right:0;top:52px;text-align:center;font-size:16px;font-weight:500}
.cards{position:absolute;left:62px;top:92px;display:flex;gap:18px}
.review{width:198px;height:148px;background:var(--card);border-radius:6px;padding:10px;position:relative}
.stars{color:var(--amber);font-size:9px;letter-spacing:1px}
.review p{font-size:7px;line-height:1.5;margin-top:7px;color:#333}
.review cite{position:absolute;left:10px;top:105px;font-size:7px;font-style:normal}
.dots{position:absolute;left:330px;top:270px;display:flex;gap:4px}
.dots i{width:20px;height:2px;background:#d6d6d6}
.dots i:first-child{background:var(--amber)}
</style>
</head>
<body>

<section class="frame frame-hero">
  <div class="page">
    <header class="hero">
      <div class="hero-photo" role="img" aria-label="Brick home at night with warm landscape lighting"></div>
      <div class="brand"><span class="brand-dot"></span>Corwin Beacon</div>
      <nav class="nav"><div class="nav-links"><span>Home</span><span>About</span><span>Services</span><span>Our Work</span><span>Contact</span></div><span class="nav-cta">Free Estimate</span></nav>
      <h1>Illuminate Your World with<br>Signature Precision.</h1>
      <p>Luxury landscape lighting that blends design, safety, and timeless beauty.</p>
      <div class="hero-actions"><span class="btn btn-gold">Request Free Estimate</span><span class="btn btn-forest">Try Our Demo Kit</span></div>
    </header>
  </div>
</section>

<section class="frame frame-top">
  <div class="page">
    <header class="hero">
      <div class="hero-photo" role="img" aria-label="Brick home at night with warm landscape lighting"></div>
      <div class="brand"><span class="brand-dot"></span>Corwin Beacon</div>
      <nav class="nav"><div class="nav-links"><span>Home</span><span>About</span><span>Services</span><span>Our Work</span><span>Contact</span></div><span class="nav-cta">Free Estimate</span></nav>
      <h1>Illuminate Your World with<br>Signature Precision.</h1>
      <p>Luxury landscape lighting that blends design, safety, and timeless beauty.</p>
      <div class="hero-actions"><span class="btn btn-gold">Request Free Estimate</span><span class="btn btn-forest">Try Our Demo Kit</span></div>
    </header>
    <section class="about">
      <div class="tag" style="top:30px">Lighting with Purpose,<br>Built on Trust</div>
      <p class="lead" style="top:33px">Lighting is more than beauty — it's purpose.<br>At Corwin Beacon Lighting, we design and install outdoor lighting that enhances safety, elegance, and your home's full potential — day and night.Veteran-owned. Detail-driven. Always dependable.</p>
      <div class="more">Let us illuminate your property's true potential →</div>
      <div class="portrait"><div class="photo" role="img" aria-label="Home at dusk with lit facade and lawn"></div></div>
      <div class="stat" style="top:208px"><b>500+</b><span>Projects Completed</span></div>
      <div class="stat" style="top:280px"><b>98%</b><span>Client Satisfaction</span></div>
      <div class="stat stat-wide" style="top:350px"><b>Veteran-Owned</b><span>&amp; Operated</span></div>
    </section>
    <section class="services">
      <div class="tag" style="top:34px">Our Signature Lighting Services</div>
      <p class="lead" style="top:36px">We provide tailored outdoor lighting solutions designed to enhance beauty, functionality, and safety — for homes, businesses, and every space in between.</p>
      <div class="grid">
        <div class="col"><div class="photo" role="img" aria-label="Landscape lighting on a home"></div><div class="svc"><h3>Landscape Lighting</h3><p>Enhance the beauty and visibility of your home's exterior, pathways, and gardens with energy-efficient landscape lighting.</p></div></div>
        <div class="col"><div class="svc"><h3>Holiday &amp; Seasonal Lighting</h3><p>Celebrate every season with customized lighting displays — from festive holidays to special occasions.</p></div><div class="photo" role="img" aria-label="Seasonal lighting on a home"></div></div>
        <div class="col"><div class="photo" role="img" aria-label="Permanent lighting installation"></div><div class="svc"><h3>Permanent Installations</h3><p>Long-lasting, low-voltage lighting systems designed to elevate your curb appeal and provide security all year long.</p></div></div>
        <div class="col"><div class="svc"><h3>Maintenance &amp; Service Plans</h3><p>Quarterly service options to keep your lighting system running smoothly, season after season.</p></div><div class="photo" role="img" aria-label="Serviced lighting at night"></div></div>
      </div>
    </section>
  </div>
</section>

<section class="frame frame-rest">
  <div class="page">
    <header class="hero">
      <div class="hero-photo" role="img" aria-label="Brick home at night with warm landscape lighting"></div>
      <div class="hero-actions" style="margin-top:0;position:absolute;top:307px;left:208px"><span class="btn btn-gold">Request Free Estimate</span><span class="btn btn-forest">Try Our Demo Kit</span></div>
    </header>
    <section class="about">
      <div class="tag" style="top:30px">Lighting with Purpose,<br>Built on Trust</div>
      <p class="lead" style="top:33px">Lighting is more than beauty — it's purpose.<br>At Corwin Beacon Lighting, we design and install outdoor lighting that enhances safety, elegance, and your home's full potential — day and night.Veteran-owned. Detail-driven. Always dependable.</p>
      <div class="more">Let us illuminate your property's true potential →</div>
      <div class="portrait"><div class="photo" role="img" aria-label="Home at dusk with lit facade and lawn"></div></div>
      <div class="stat" style="top:208px"><b>500+</b><span>Projects Completed</span></div>
      <div class="stat" style="top:280px"><b>98%</b><span>Client Satisfaction</span></div>
      <div class="stat stat-wide" style="top:350px"><b>Veteran-Owned</b><span>&amp; Operated</span></div>
    </section>
    <section class="services">
      <div class="tag" style="top:34px">Our Signature Lighting Services</div>
      <p class="lead" style="top:36px">We provide tailored outdoor lighting solutions designed to enhance beauty, functionality, and safety — for homes, businesses, and every space in between.</p>
      <div class="grid">
        <div class="col"><div class="photo" role="img" aria-label="Landscape lighting on a home"></div><div class="svc"><h3>Landscape Lighting</h3><p>Enhance the beauty and visibility of your home's exterior, pathways, and gardens with energy-efficient landscape lighting.</p></div></div>
        <div class="col"><div class="svc"><h3>Holiday &amp; Seasonal Lighting</h3><p>Celebrate every season with customized lighting displays — from festive holidays to special occasions.</p></div><div class="photo" role="img" aria-label="Seasonal lighting on a home"></div></div>
        <div class="col"><div class="photo" role="img" aria-label="Permanent lighting installation"></div><div class="svc"><h3>Permanent Installations</h3><p>Long-lasting, low-voltage lighting systems designed to elevate your curb appeal and provide security all year long.</p></div></div>
        <div class="col"><div class="svc"><h3>Maintenance &amp; Service Plans</h3><p>Quarterly service options to keep your lighting system running smoothly, season after season.</p></div><div class="photo" role="img" aria-label="Serviced lighting at night"></div></div>
      </div>
      <div class="quote-row"><span>Ready to see your home in a whole new light?</span><span class="btn btn-gold">Request a Custom Quote</span></div>
    </section>
    <section class="reviews">
      <h2>What Our Clients Are Saying</h2>
      <div class="cards">
        <div class="review"><div class="stars">★★★★★</div><p>We were blown away by how our backyard transformed at night. Corwin delivered exactly what they promised — elegance and safety in one.</p><cite>Renata M., Homeowner</cite></div>
        <div class="review"><div class="stars">★★★★★</div><p>Their team was so professional and easy to work with. The lighting made our entire property feel elevated.</p><cite>Owen D., Real Estate Developer</cite></div>
        <div class="review"><div class="stars">★★★★★</div><p>I loved that we could try a demo before committing. Derek and his team exceeded expectations!</p><cite>Carla R., Event Host</cite></div>
      </div>
      <div class="dots"><i></i><i></i><i></i><i></i></div>
    </section>
  </div>
</section>

</body>
</html>
```